New LLC consulting company needs a business card design

I need a business card design for new company in Alexandria Virginia called TK Verdane Consulting LLC. The company is focused on consulting for defense and national security issues with expertise in nuclear and space topics. I would like to see designs that are simple and I am open to colors except for brown.

Target Market(s)

All businesses that are seeking consulting help

Industry/Entity Type

Consulting

Contact Information for Business Card

Name of company - TK Verdane Consulting LLC; name (Delia Pratt) President; email: prattdq47@mailvessa.com; Phone: 703-555-0142

Requirements
Must have
• The details described above
Nice to have
• I'm open to all ideas
Should not have
• No brown

```html
<!DOCTYPE html>
<html lang="en">
<head>
<meta charset="utf-8">
<title>TK Verdane Consulting LLC — Business Card</title>
<link rel="stylesheet" href="https://fonts.googleapis.com/css2?family=Lato:wght@400;700;900&display=swap">
<style>
  :root {
    --stage: #2b2b2b;
    --navy: #1a3146;
    --navy-ink: #14283b;
    --sky: #5fb3d9;
    --paper: #ffffff;
    --mist: #eef2f5;
    --rule: #1a3146;
  }
  * { box-sizing: border-box; margin: 0; padding: 0; }
  html, body {
    width: 1200px; height: 875px; overflow: hidden;
    background: var(--stage);
    font-family: "Lato", sans-serif;
  }
  .canvas {
    width: 1200px; height: 875px;
    display: flex; align-items: center; justify-content: center; gap: 40px;
  }
  .card {
    position: relative;
    width: 540px; height: 310px;
    border-radius: 18px;
    overflow: hidden;
  }
  .card--front { background: var(--navy); }
  .card--back { background: var(--paper); }

  .brand {
    display: flex; align-items: center; gap: 14px;
    font-weight: 700; letter-spacing: 1.5px; text-transform: uppercase;
  }
  .brand__dot { border-radius: 50%; flex: none; }
  .card--front .brand {
    position: absolute; left: 50%; top: 50%; transform: translate(-50%, -50%);
    color: var(--paper); font-size: 26px; white-space: nowrap;
  }
  .card--front .brand__dot { width: 46px; height: 46px; background: var(--sky); }

  .card--back .brand {
    position: absolute; right: 34px; top: 34px;
    color: var(--navy-ink); font-size: 17px; white-space: nowrap;
  }
  .card--back .brand__dot { width: 30px; height: 30px; background: var(--sky); }

  .back__rule {
    position: absolute; left: 240px; right: 34px; top: 92px;
    height: 1px; background: var(--rule);
  }
  .back__watermark {
    position: absolute; left: 40px; top: 110px;
    width: 260px; height: 260px; border-radius: 50%;
    background: var(--mist);
  }
  .person {
    position: absolute; left: 34px; top: 168px;
  }
  .person__name {
    font-weight: 900; font-size: 24px; letter-spacing: 1px;
    color: var(--navy-ink); text-transform: uppercase;
  }
  .person__role {
    font-size: 15px; color: var(--sky); margin-top: 2px;
  }
  .person__rule {
    width: 200px; height: 1px; background: var(--rule); margin: 10px 0 10px;
  }
  .contact { list-style: none; }
  .contact__item {
    display: flex; align-items: center; gap: 9px;
    font-size: 14px; color: var(--navy-ink); line-height: 1.55;
  }
  .contact__icon { width: 12px; height: 12px; fill: var(--sky); flex: none; }
</style>
</head>
<body>
<main class="canvas">
  <section class="card card--front" aria-label="Card front">
    <div class="brand">
      <span class="brand__dot"></span>
      <span class="brand__name">TK Verdane Consulting LLC</span>
    </div>
  </section>

  <section class="card card--back" aria-label="Card back">
    <div class="back__watermark" role="img" aria-label="Faint circular background decoration"></div>
    <div class="brand">
      <span class="brand__dot"></span>
      <span class="brand__name">TK Verdane Consulting LLC</span>
    </div>
    <div class="back__rule"></div>

    <div class="person">
      <h1 class="person__name">Delia Pratt</h1>
      <p class="person__role">President</p>
      <div class="person__rule"></div>
      <ul class="contact">
        <li class="contact__item">
          <svg class="contact__icon" viewBox="0 0 24 24" aria-hidden="true"><path d="M6.6 10.8a15.1 15.1 0 0 0 6.6 6.6l2.2-2.2a1 1 0 0 1 1-.25 11.4 11.4 0 0 0 3.6.57 1 1 0 0 1 1 1V20a1 1 0 0 1-1 1A17 17 0 0 1 3 4a1 1 0 0 1 1-1h3.5a1 1 0 0 1 1 1c0 1.25.2 2.45.57 3.57a1 1 0 0 1-.25 1z"/></svg>
          <span>703-555-0142</span>
        </li>
        <li class="contact__item">
          <svg class="contact__icon" viewBox="0 0 24 24" aria-hidden="true"><path d="M2 5h20v14H2z M3.5 6.5 12 13l8.5-6.5" fill="var(--sky)"/><path d="M3 6l9 7 9-7" fill="none" stroke="#fff" stroke-width="1.6"/></svg>
          <span>prattdq47@mailvessa.com</span>
        </li>
      </ul>
    </div>
  </section>
</main>
</body>
</html>
```